Velora Kestrel Glide Toothbrush Backcard Design

We need a toothbrush backcard (toothbrush packaging) design for our new toothbrush. We are one of the leading toothbrush distributor and producer company. At the moment our toothbrushes are selling at Marvo, Sunway Depot, 9-Twenty and many more supermarkets and mom-and-pop shops in Thailand. Our toothbrush is emphasized on the soft and slim tip bristles which will not hurt your enamel. Easy to grip handle that will ease of use. These 2 mains point should be communicated through the design.

Our brand name is Velora (see attached logo that you can use) and the toothbrush model is Kestrel Glide. We will have 2 series for this model which are Kestrel Glide Extra Soft and Kestrel Glide Medium soft. They are basically differentiated by its packaging colors.

We are looking for the attractive and outstanding design from what available in the market right now. Please see enclosed die cut shape of the packaging. This backcard will hold 3 pieces of toothbrush with clear blister cover.

P.S We are very confident that our product produced with very good quality that's why we want to attract people to try. So when they walk in the aisle we want our toothbrush packaging to be eye catching and welcome customer to try.

Target Market(s)

B+ household consumers age between 18-65 both men and women who has open minded to the new product and willing to spend money without brand royalty.

Font styles to use
Sans Serif

Colors

Designer to choose colors to be used in the design.

Requirements
Must have
• - Logo, and model name
• - Quality mark as following GMP, NHB, ISO9001:2015, ISO22176
• - Attractive character which attract the target clients to try.
• - 2-sided packaging using attached die cut
Nice to have
Should not have
• What other brands have

```html
<!DOCTYPE html>
<html lang="en">
<head>
<meta charset="utf-8">
<title>Velora Kestrel Glide – Backcard Front and Back</title>
<link rel="stylesheet" href="https://fonts.googleapis.com/css2?family=Rubik:wght@500;700;800&family=Montserrat:wght@400;500&display=swap">
<style>
  :root{
    --navy:#2b2d78;
    --green:#14a04a;
    --yellow:#fdd20a;
    --amber:#f7a51c;
    --crimson:#d6173f;
    --plum:#2d1440;
    --violet:#4a2166;
    --gold:#f5b731;
    --frame:#55b8e8;
    --white:#ffffff;
    --ink:#111111;
    --brush-light:#f4f6f6;
    --brush-teal:#5fd0b8;
  }
  *{box-sizing:border-box;margin:0;padding:0}
  html,body{width:926px;height:1200px;overflow:hidden;background:var(--white)}
  .canvas{position:relative;width:926px;height:1200px}
  .backcard{position:absolute;top:46px;width:338px;height:1116px;border-radius:30px;overflow:hidden;border:1.5px solid var(--frame)}
  .backcard--front{left:84px}
  .backcard--back{left:510px}
  .backcard__art{position:absolute;inset:0}
  .backcard--front .backcard__art{
    background:linear-gradient(172deg,var(--navy) 0%,var(--navy) 10%,var(--green) 24%,var(--yellow) 42%,var(--amber) 52%,var(--crimson) 64%,var(--plum) 84%,var(--violet) 100%);
  }
  .backcard--back .backcard__art{
    background:linear-gradient(186deg,var(--navy) 0%,var(--green) 16%,var(--yellow) 34%,var(--amber) 50%,var(--crimson) 62%,var(--plum) 84%,var(--violet) 100%);
  }
  .inner-frame{position:absolute;left:23px;top:23px;width:292px;height:1070px;border:1px solid var(--frame);border-radius:24px;pointer-events:none}
  .hang-box{position:absolute;top:63px;height:73px;width:188px;border:1px solid var(--frame);border-radius:14px}
  .hang-slot{position:absolute;top:82px;height:36px;width:200px;background:var(--white);border-radius:14px;border:1px solid var(--frame)}
  .model-title{position:absolute;left:0;width:338px;text-align:center;font-family:'Rubik',sans-serif;font-weight:700;color:var(--gold);white-space:nowrap}
  .brand-word{position:absolute;font-family:'Rubik',sans-serif;font-weight:800;color:var(--white);white-space:nowrap;letter-spacing:.5px}
  .brand-word--vertical{color:var(--gold);writing-mode:vertical-rl;transform:rotate(180deg)}
  .product-art{position:absolute;left:48px;top:142px;width:258px;height:878px;border-radius:40px;
    background:linear-gradient(180deg,var(--brush-light) 0%,var(--brush-light) 45%,var(--brush-teal) 75%,var(--brush-light) 100%);opacity:.92}
  .features{position:absolute;left:38px;top:1030px;list-style:none;font-family:'Montserrat',sans-serif;font-size:12.5px;color:var(--white)}
  .features li{display:flex;align-items:center;gap:6px;height:26px}
  .features .mark{width:10px;height:10px;background:var(--gold);transform:rotate(45deg);border-radius:2px}
  .badges{position:absolute;display:flex;gap:6px;align-items:center}
  .badge{background:var(--white)}
  .badge--round{border-radius:50%}
  .badge--dark{background:var(--ink)}
  .vertical-copy{position:absolute;writing-mode:vertical-rl;transform:rotate(180deg);font-family:'Montserrat',sans-serif;color:var(--ink)}
  .benefits{left:42px;top:410px;height:350px;font-size:13.5px;line-height:20px;list-style:none}
  .benefits li{display:flex;gap:6px;align-items:center}
  .benefits .star{font-size:14px}
  .maker{left:212px;top:438px;height:126px;font-size:12px;line-height:16px}
</style>
</head>
<body>
<main class="canvas">

  <section class="backcard backcard--front" aria-label="Front of backcard">
    <div class="backcard__art" role="img" aria-label="Colourful flowing background in navy, green, yellow, red and purple"></div>
    <div class="inner-frame"></div>
    <h1 class="model-title" style="top:26px;font-size:30px">Kestrel Glide</h1>
    <div class="hang-box" style="left:126px"></div>
    <div class="hang-slot" style="left:154px"></div>
    <div class="product-art" role="img" aria-label="Three white and mint toothbrushes with soft slim tip bristles"></div>
    <div class="brand-word brand-word--vertical" style="left:34px;top:300px;font-size:34px">Velora</div>
    <ul class="features">
      <li><span class="mark"></span>Soft And Slim Tip Bristles</li>
      <li><span class="mark"></span>Easy to grip handle</li>
    </ul>
    <div class="badges" style="left:214px;top:1052px" aria-label="Quality marks">
      <span class="badge badge--round" style="width:18px;height:18px"></span>
      <span class="badge" style="width:28px;height:14px;border-radius:3px"></span>
      <span class="badge" style="width:30px;height:14px;border-radius:3px"></span>
    </div>
  </section>

  <section class="backcard backcard--back" aria-label="Back of backcard">
    <div class="backcard__art" role="img" aria-label="Colourful flowing background in navy, green, yellow, red and purple"></div>
    <div class="inner-frame"></div>
    <div class="hang-box" style="left:23px"></div>
    <div class="hang-slot" style="left:-16px"></div>
    <ul class="vertical-copy benefits">
      <li><span class="star">✦</span>Our toothbrush is emphasized on the soft and</li>
      <li><span class="star">✦</span>slim tip bristles which will not hurt your enamel</li>
      <li>&nbsp;&nbsp;&nbsp;&nbsp;Easy to grip handle that will ease of use</li>
    </ul>
    <p class="vertical-copy maker">Manufactured for<br>Velora Home Care Co.<br>Street , City<br>1-555-010-2040<br>Made Country</p>
    <div class="badges" style="left:258px;top:588px;flex-direction:column;gap:14px" aria-label="Quality marks">
      <span class="badge badge--dark" style="width:22px;height:44px;border-radius:3px"></span>
      <span class="badge badge--dark" style="width:22px;height:40px;border-radius:3px"></span>
      <span class="badge badge--dark badge--round" style="width:24px;height:24px"></span>
    </div>
    <div class="brand-word" style="left:0;width:338px;top:968px;text-align:center;font-size:50px">Velora</div>
    <h2 class="model-title" style="top:1036px;font-size:34px">Kestrel Glide</h2>
  </section>

</main>
</body>
</html>
```